Working Capital graphics

Our business advisory firm requires 9 images to be re-created and improved in the branding of our business.

The 9 images have been uploaded below and the colours and branding of the business can be found at the website www.tallowmereadvisory.com.au

```html
<!DOCTYPE html>
<html lang="en">
<head>
<meta charset="utf-8">
<title>Next $100 of Sales Volume – Working Capital Cycle</title>
<link rel="stylesheet" href="https://fonts.googleapis.com/css2?family=Josefin+Sans:wght@600;700&family=Oswald:wght@600&display=swap">
<style>
  :root {
    --ink-navy: #0e2150;
    --ring-line: #1b2f6e;
    --dot-blue: #5ec8f8;
    --accent-orange: #f3932f;
    --sky-cyan: #35bdf2;
    --sales-blue: #22a8e3;
    --shortfall-blue: #5fc9f8;
    --debt-blue: #1650bc;
    --capital-blue: #0e3783;
    --deep-navy: #0a2350;
    --paper: #ffffff;
  }
  html, body {
    margin: 0;
    padding: 0;
    width: 1200px;
    height: 1055px;
    overflow: hidden;
    background: var(--paper);
  }
  .cycle-diagram {
    display: block;
    width: 1200px;
    height: 1055px;
  }
  .outer-ring { fill: none; stroke: var(--ring-line); stroke-width: 2.5; }
  .connector { stroke: var(--ring-line); stroke-width: 2.5; }
  .anchor-dot { fill: var(--dot-blue); stroke: var(--paper); stroke-width: 6; }
  .metric-ring { fill: var(--paper); stroke: var(--dot-blue); stroke-width: 2.5; }
  .metric-ring-accent { fill: none; stroke: var(--accent-orange); stroke-width: 2.5; }
  .metric-label {
    font-family: "Josefin Sans", "Century Gothic", sans-serif;
    font-weight: 700;
    fill: var(--ink-navy);
    text-anchor: middle;
    letter-spacing: 2px;
  }
  .segment { stroke: none; }
  .segment--cash { fill: var(--sky-cyan); }
  .segment--sales { fill: var(--sales-blue); }
  .segment--opex { fill: var(--accent-orange); }
  .segment--payouts { fill: var(--deep-navy); }
  .segment--capital { fill: var(--capital-blue); }
  .segment--debt { fill: var(--debt-blue); }
  .segment--shortfall { fill: var(--shortfall-blue); }
  .segment-label {
    font-family: "Josefin Sans", "Century Gothic", sans-serif;
    font-weight: 600;
    fill: var(--paper);
    text-anchor: middle;
    letter-spacing: 3px;
  }
  .headline {
    font-family: "Oswald", "Futura", sans-serif;
    font-weight: 600;
    fill: var(--accent-orange);
    text-anchor: middle;
  }
</style>
</head>
<body>
<svg class="cycle-diagram" viewBox="0 0 2040 1794" xmlns="http://www.w3.org/2000/svg" role="img" aria-label="Cycle showing how the next $100 of sales volume flows through costs, working capital and funding">
  <defs>
    <path id="sales-arc" d="M1096.2 494.2 A410 410 0 0 1 1380.1 693"/>
  </defs>

  <circle class="outer-ring" cx="1025" cy="898" r="551"/>

  <line class="connector" x1="1010" y1="276" x2="1010" y2="347"/>
  <line class="connector" x1="1522" y1="659" x2="1588" y2="630"/>
  <line class="connector" x1="1506" y1="1169" x2="1566" y2="1205"/>
  <line class="connector" x1="1041" y1="1449" x2="1041" y2="1520"/>
  <line class="connector" x1="523" y1="1128" x2="458" y2="1156"/>
  <line class="connector" x1="535" y1="644" x2="474" y2="610"/>

  <circle class="anchor-dot" cx="1010" cy="347" r="11"/>
  <circle class="anchor-dot" cx="1522" cy="659" r="11"/>
  <circle class="anchor-dot" cx="1506" cy="1169" r="11"/>
  <circle class="anchor-dot" cx="1041" cy="1449" r="11"/>
  <circle class="anchor-dot" cx="523" cy="1128" r="11"/>
  <circle class="anchor-dot" cx="535" cy="644" r="11"/>

  <!-- cycle segments -->
  <path class="segment segment--cash" d="M798 440 A510 510 0 0 1 978 390 L1095 465 L1025 567 A330 330 0 0 0 888 598 L928 493 Z"/>
  <path class="segment segment--sales" d="M1002 387 A510 510 0 0 1 1416 567 L1418 707 L1295 707 A330 330 0 0 0 1041 568 L1110 465 Z"/>
  <path class="segment segment--opex" d="M1430 585 L1432 720 L1305 720 A330 330 0 0 1 1316 1057 L1368 1168 L1495 1105 A510 510 0 0 0 1430 585 Z"/>
  <path class="segment segment--payouts" d="M1125 1400 L1003 1335 L1060 1228 A330 330 0 0 0 1310 1072 L1364 1184 L1483 1125 A510 510 0 0 1 1125 1400 Z"/>
  <path class="segment segment--capital" d="M623 1215 A510 510 0 0 0 1103 1403 L985 1337 L1045 1228 A330 330 0 0 1 748 1082 L628 1075 Z"/>
  <path class="segment segment--debt" d="M568 667 L697 612 L742 725 A330 330 0 0 0 740 1067 L613 1062 L610 1195 A510 510 0 0 1 568 667 Z"/>
  <path class="segment segment--shortfall" d="M580 650 A510 510 0 0 1 782 448 L913 497 L867 608 A330 330 0 0 0 752 712 L705 596 Z"/>

  <!-- segment labels -->
  <text class="segment-label" font-size="34" x="984" y="490" transform="rotate(-4 984 478)">0$</text>
  <text class="segment-label" font-size="34" letter-spacing="5"><textPath href="#sales-arc" startOffset="50%">COST OF SALES</textPath></text>
  <g transform="rotate(-32 805 560)">
    <text class="segment-label" font-size="26" x="805" y="550">CASH</text>
    <text class="segment-label" font-size="26" x="805" y="582">SORTFALL</text>
  </g>
  <g transform="rotate(-90 1444 855)">
    <text class="segment-label" font-size="26" x="1444" y="846">OPERATING</text>
    <text class="segment-label" font-size="26" x="1444" y="884">EXPEMNSEES</text>
  </g>
  <g transform="rotate(-62 1413 1033)">
    <text class="segment-label" font-size="26" x="1413" y="1024">COSTS</text>
    <text class="segment-label" font-size="26" x="1413" y="1060">FIXED</text>
  </g>
  <text class="segment-label" font-size="22" letter-spacing="2" x="1103" y="1323" textLength="132" lengthAdjust="spacingAndGlyphs" transform="rotate(-12 1103 1315)">DIVIDENDS</text>
  <text class="segment-label" font-size="22" letter-spacing="2" x="1238" y="1276" textLength="100" lengthAdjust="spacingAndGlyphs" transform="rotate(-26 1238 1268)">INTEREST</text>
  <text class="segment-label" font-size="22" letter-spacing="2" x="1322" y="1216" textLength="42" lengthAdjust="spacingAndGlyphs" transform="rotate(-40 1322 1208)">TAX</text>
  <g transform="rotate(55 677 1165)">
    <text class="segment-label" font-size="22" x="677" y="1160">AR</text>
    <text class="segment-label" font-size="22" x="677" y="1186">DAYS</text>
  </g>
  <g transform="rotate(35 782 1280)">
    <text class="segment-label" font-size="22" x="782" y="1275">AP</text>
    <text class="segment-label" font-size="22" x="782" y="1301">DAYS</text>
  </g>
  <g transform="rotate(15 922 1340)">
    <text class="segment-label" font-size="22" x="922" y="1335">INV</text>
    <text class="segment-label" font-size="22" x="922" y="1361">DAYS</text>
  </g>
  <g transform="rotate(-90 622 848)">
    <text class="segment-label" font-size="32" x="622" y="840">ADDITIONAL</text>
    <text class="segment-label" font-size="32" x="622" y="885">DEBT</text>
  </g>

  <text class="headline" font-size="88" x="1025" y="878" textLength="512" lengthAdjust="spacingAndGlyphs">NEXT $100 OF</text>
  <text class="headline" font-size="88" x="1025" y="966" textLength="512" lengthAdjust="spacingAndGlyphs">SALES VOLUME</text>

  <!-- metric circles -->
  <g class="metric metric--revenue">
    <circle class="metric-ring" cx="1010" cy="183" r="93"/>
    <path class="metric-ring-accent" d="M1010 90 A93 93 0 0 0 1010 276"/>
    <text class="metric-label" font-size="24" x="1010" y="176">REVENUE</text>
    <text class="metric-label" font-size="24" x="1010" y="206">0$</text>
  </g>
  <g class="metric metric--gross-margins">
    <circle class="metric-ring" cx="1672" cy="593" r="93"/>
    <path class="metric-ring-accent" d="M1672 500 A93 93 0 0 1 1672 686"/>
    <text class="metric-label" font-size="24" x="1672" y="578">GROSS</text>
    <text class="metric-label" font-size="24" x="1672" y="607">MARGINS</text>
    <text class="metric-label" font-size="24" x="1672" y="636">0$</text>
  </g>
  <g class="metric metric--ebit">
    <circle class="metric-ring" cx="1646" cy="1253" r="93"/>
    <path class="metric-ring-accent" d="M1553 1253 A93 93 0 0 0 1646 1346"/>
    <text class="metric-label" font-size="27" x="1646" y="1246">EBIT</text>
    <text class="metric-label" font-size="27" x="1646" y="1280">0$</text>
  </g>
  <g class="metric metric--retained-income">
    <circle class="metric-ring" cx="1041" cy="1613" r="93"/>
    <path class="metric-ring-accent" d="M1041 1520 A93 93 0 0 0 1041 1706"/>
    <text class="metric-label" font-size="22" x="1041" y="1598">RETAINED</text>
    <text class="metric-label" font-size="22" x="1041" y="1623">INCOME</text>
    <text class="metric-label" font-size="22" x="1041" y="1648">0$</text>
  </g>
  <g class="metric metric--after-working-capital">
    <circle class="metric-ring" cx="373" cy="1191" r="93"/>
    <path class="metric-ring-accent" d="M373 1098 A93 93 0 0 0 373 1284"/>
    <text class="metric-label" font-size="21" x="371" y="1163">AFTER</text>
    <text class="metric-label" font-size="21" x="371" y="1187">WORKING</text>
    <text class="metric-label" font-size="21" x="371" y="1211">CAPITAL</text>
    <text class="metric-label" font-size="21" x="371" y="1235">0$</text>
  </g>
  <g class="metric metric--after-funding">
    <circle class="metric-ring" cx="392" cy="565" r="93"/>
    <path class="metric-ring-accent" d="M392 472 A93 93 0 0 0 392 658"/>
    <text class="metric-label" font-size="21" x="392" y="533">AFTER</text>
    <text class="metric-label" font-size="21" x="392" y="559">ADDITIONAL</text>
    <text class="metric-label" font-size="21" x="392" y="585">FUNDING</text>
    <text class="metric-label" font-size="21" x="392" y="611">0$</text>
  </g>
</svg>
</body>
</html>
```